Web Design Project for a Software & Consulting Company

We have just completed a recent ArtHerdly project for a new logo (see attached).
As the next stage of our rebranding we now require a website re-design to complement the new logo.
Our current site, http://www.corvinsoft.example was built in-house and does not come across as professional as we would like. We supply software and associated services to some of the world’s largest oil companies and we need our site to reflect that level of client.
We will also be posting another design project for brochures, PowerPoint slides and other materials very soon.
We would like designs for…
Home page
Product page
• TZQ
• BLV
• PNJ
Services
News page
About Us page
Contact Us page
Page for mobile devices that gives basic company and product information
Currently the site is small but we intend to increase content to include white papers etc. this should be taken into account when designing the navigation therefore we would prefer navigation through styled text links rather than images.
Colour schemes should broadly be taken from our new logo, where the dark blue and dark green from the left and right sides of the logo are the main colours, but other, brighter accent colours can be used to highlight sections or content.
Dark Blue = C:88, M:55, Y:44, K:28
Dark Green = C:87, M:53, Y:50, K:50
NB: Don’t use the logo on our current site, make sure you use the one attached.
We would prefer the final file format to be a layered PSD.
The site should be clean and professional and communicate the following...
• That we have a great depth and breadth of knowledge about our customers’ business, enabling us to deliver the best systems and solutions.
• That we are a leading provider of cost estimation and control solutions to the oil and gas industry.
• The benefits of our software and consulting services.
• Show that we deliver outstanding customer service and value with a very high level of professionalism
• The site should have no Flash and be able to self-adjust to fit any screen size.
Things to avoid …
• Obvious and clichéd oil industry imagery, no oil rigs
• Cartoon style graphics
Our Background
We are an integrated software and consulting organization specialising in the drilling side of the oil and gas industry. Simply put our software helps companies better understand, predict and communicate the cost of drilling wells.
We have 3 software products and a consulting offering consisting of…
• TZQ - Probabilistic time and cost software
• BLV – Cost tracking and reporting software
• PNJ – (currently known as DrillSavant) – Lessons learned software
• Consulting services
Our systems are in use in over 30 countries with a broad range of clients including: GN, Marovel, Dunt, Koruna, VELO Sirkami, FALUMI and Quintex.
Our current site can be found at www.corvinsoft.example
Our main competitors are
• http://www.drovanic.example/
• http://www.sumbrask.example/
• http://www.kve.example/services/software-solutions/p1-
Our depth of drilling knowledge, quality of software and collaboration with clients differentiate us form the competition.
We strive for very high levels of customer service.
We look forward to receiving your designs!
Updates
Thanks to all the designers who have submitted a design, we appreciate the effort.
We will do our best to give individual feedback on each design but given that many are quite similar we thought we would give some general feedback first.
Nearly all the designs submitted so far have been slight variations on…
-
Top Menu
-
Scrolling Photo Banner
-
4 Columns
-
Body
-
Deep Footer
These designs are well executed but they are basically the same layout as our existing site and while there is nothing inherently wrong with this layout we would like to see some designs that are a bit more innovative and different. We don’t really want just a polished version of our current site.
Thanks again,
CVS
Thanks to everyone who has submitted a design, the response has been great.
We are close to making a decision so if you are intending to submit a design please do it soon, the deadline is only a few days away.
Thanks again.
CVS
Target Market(s)
Mid to high level executives
Industry/Entity Type
Oil And Gas
Look and feel

```html
<!DOCTYPE html>
<html lang="en">
<head>
<meta charset="utf-8">
<title>Corvin Software</title>
<link href="https://fonts.googleapis.com/css2?family=Ubuntu:wght@400;500&family=Open+Sans:wght@400;600&display=swap" rel="stylesheet">
<style>
:root{
  --teal:#1f4b5e;
  --teal-dark:#17394a;
  --link-blue:#1d5f8e;
  --text:#6b6b6b;
  --heading:#555;
  --rule:#c8c8c8;
  --footer:#3e3e3e;
  --footer-bar:#333;
  --footer-text:#e6e6e6;
  --white:#fff;
}
*{margin:0;padding:0;box-sizing:border-box}
html,body{width:929px;height:1200px;overflow:hidden;background:var(--white)}
body{position:relative;font-family:"Open Sans",sans-serif;color:var(--text)}
.abs{position:absolute}

/* header */
.brand{left:103px;top:24px;font-family:"Ubuntu",sans-serif;font-weight:500;font-size:19px;color:var(--teal);letter-spacing:.5px}
.nav{left:415px;top:33px;display:flex;align-items:center;gap:0;font-family:"Open Sans",sans-serif;font-size:10px}
.nav a{color:#666;text-decoration:none;padding:0 13px;line-height:26px}
.nav a.active{background:var(--teal);color:var(--white);border-radius:2px;padding:0 8px;margin-right:9px}
.social{left:759px;top:36px;display:flex;gap:5px}
.social span{width:18px;height:18px;border-radius:50%;background:#777;display:block}

/* hero */
.hero{left:0;top:91px;width:929px;height:357px;background:radial-gradient(ellipse 60% 45% at 40% 25%,#e7d9b0 0%,#8a9bb3 25%,transparent 60%),linear-gradient(160deg,#0d1a33 0%,#2b4a72 40%,#3f6994 60%,#1a3556 100%)}
.hero-title{left:118px;top:154px;width:360px;font-family:"Ubuntu",sans-serif;font-size:29px;line-height:35px;color:var(--white);text-shadow:0 1px 3px rgba(0,0,0,.5)}
.hero-copy{left:120px;top:274px;width:330px;font-size:9.6px;line-height:15.6px;color:var(--white);text-shadow:0 1px 2px rgba(0,0,0,.6)}
.hero-device{left:495px;top:140px;width:310px;height:252px;background:linear-gradient(180deg,#1b2433 0%,#3a5575 60%,#c9ccd0 78%,#e5e5e5 100%);border-radius:8px;opacity:.92}

/* features */
.feature{top:474px;width:170px;text-align:center}
.feature .disc{width:97px;height:97px;border-radius:50%;background:var(--teal);margin:0 auto;display:flex;align-items:center;justify-content:center}
.feature h3{font-family:"Ubuntu",sans-serif;font-weight:400;font-size:20px;color:var(--heading);margin-top:16px}
.feature p{text-align:left;font-size:9.6px;line-height:13.2px;margin:11px 0 0 18px;width:142px}

/* welcome */
.welcome-title{left:111px;top:737px;font-family:"Ubuntu",sans-serif;font-size:16px;color:var(--link-blue);letter-spacing:.2px}
.welcome-copy{left:112px;top:765px;width:700px;font-size:10.4px;line-height:15.6px}

/* clients */
.clients-rule{left:102px;top:863px;width:724px;height:1px;background:var(--rule)}
.clients-label{left:414px;top:852px;padding:0 11px;background:var(--white);font-family:"Ubuntu",sans-serif;font-size:15px;color:#555}
.client-row{left:110px;top:894px;width:716px;height:30px;display:flex;justify-content:space-between;align-items:center}
.client{font-family:"Ubuntu",sans-serif;font-weight:500;font-size:13px;color:#5a5a5a;display:flex;align-items:center;gap:4px}
.client i{width:9px;height:9px;border-radius:50%;background:#9a9a9a;display:block}

/* footer */
.footer{left:0;top:970px;width:929px;height:184px;background:var(--footer)}
.footer-bar{left:0;top:1154px;width:929px;height:46px;background:var(--footer-bar)}
.footer-col{top:996px;color:var(--footer-text);font-size:10.4px;line-height:19.4px}
.footer-col h4{font-family:"Open Sans",sans-serif;font-weight:600;font-size:11.5px;margin-bottom:17px;color:var(--white)}
.partner-badge{left:664px;top:1080px;width:160px;height:36px;background:#5a5a5a;border-radius:3px}
.copyright{left:121px;top:1168px;font-size:9.6px;color:var(--footer-text)}
</style>
</head>
<body>

<header>
  <div class="abs brand">CORVIN SOFTWARE</div>
  <nav class="abs nav">
    <a class="active" href="#">HOME</a>
    <a href="#">ABOUT US</a>
    <a href="#">NEWS</a>
    <a href="#">SOLUTION</a>
    <a href="#">CONTACT US</a>
  </nav>
  <div class="abs social" aria-label="Social links"><span></span><span></span><span></span></div>
</header>

<section>
  <div class="abs hero" role="img" aria-label="Night sky with a bright galaxy and stars"></div>
  <h1 class="abs hero-title" style="font-weight:400">DrillSavant Lessons Learned for the Oil and Gas Industry</h1>
  <p class="abs hero-copy">Autem vel eum iriure dolor in hendrerit in vulputate velit esse molestie consequat, vel illum qui blandit praesent feugiat nulla facilisis at vero eros et accumsan et iusto odio dignissim qui blandit praesent luptatum zzril delenit augue duis dolore te feugait nulla facilisi qui blandit praesent luptatum zzril delenit augue duis dolore te feugait nulla</p>
  <div class="abs hero-device" role="img" aria-label="Desktop monitor showing the home page, with a magnifying lens over the headline"></div>
</section>

<section>
  <div class="abs feature" style="left:94px">
    <div class="disc">
      <svg width="50" height="56" viewBox="0 0 50 56" fill="#fff"><g stroke="#fff" stroke-width="2.5" stroke-linecap="round"><line x1="25" y1="2" x2="25" y2="8"/><line x1="8" y1="10" x2="12" y2="14"/><line x1="42" y1="10" x2="38" y2="14"/><line x1="3" y1="26" x2="9" y2="26"/><line x1="47" y1="26" x2="41" y2="26"/></g><circle cx="25" cy="26" r="12"/><rect x="19" y="37" width="12" height="9" rx="2"/></svg>
    </div>
    <h3>Plan</h3>
    <p>TZQ delivers a standardized, systematic approach to understanding, quantifying and communicating the impact of project risk to all stakeholders.</p>
  </div>
  <div class="abs feature" style="left:284px">
    <div class="disc">
      <svg width="56" height="56" viewBox="0 0 56 56" fill="#fff"><rect x="14" y="16" width="28" height="24" rx="3" fill="none" stroke="#fff" stroke-width="3"/><rect x="16" y="21" width="24" height="3"/><path d="M28 3l5 6h-10zM28 53l5-6h-10zM3 28l6-5v10zM53 28l-6-5v10z"/></svg>
    </div>
    <h3>Execute</h3>
    <p>Since 1992 BLV has been helping companies optimize their materials and logistics processes and accurately track costs on a daily basis.</p>
  </div>
  <div class="abs feature" style="left:473px">
    <div class="disc">
      <svg width="50" height="50" viewBox="0 0 50 50"><g fill="#fff"><circle cx="25" cy="25" r="16"/><g><rect x="21" y="2" width="8" height="9"/><rect x="21" y="39" width="8" height="9"/><rect x="2" y="21" width="9" height="8"/><rect x="39" y="21" width="9" height="8"/><rect x="21" y="2" width="8" height="9" transform="rotate(45 25 25)"/><rect x="21" y="39" width="8" height="9" transform="rotate(45 25 25)"/><rect x="2" y="21" width="9" height="8" transform="rotate(45 25 25)"/><rect x="39" y="21" width="9" height="8" transform="rotate(45 25 25)"/></g></g><circle cx="25" cy="25" r="3.5" fill="#1f4b5e"/></svg>
    </div>
    <h3>Learn</h3>
    <p>DrillSavant is an advanced lessons learned and knowledge management system for use in the Oil &amp; Gas industry. It's fully searchable and easy to use.</p>
  </div>
  <div class="abs feature" style="left:663px">
    <div class="disc">
      <svg width="40" height="48" viewBox="0 0 40 48" fill="#fff"><rect x="2" y="2" width="36" height="44" rx="5"/><g fill="#1f4b5e"><rect x="7" y="7" width="26" height="8"/><rect x="7" y="19" width="6" height="5"/><rect x="17" y="19" width="6" height="5"/><rect x="27" y="19" width="6" height="5"/><rect x="7" y="28" width="6" height="5"/><rect x="17" y="28" width="6" height="5"/><rect x="27" y="28" width="6" height="5"/><rect x="7" y="37" width="6" height="5"/><rect x="17" y="37" width="6" height="5"/><rect x="27" y="37" width="6" height="5"/></g></svg>
    </div>
    <h3>Embed</h3>
    <p>Software solutions rely on people and processes to deliver results. From analysis through execution we support our clients to improve performance.</p>
  </div>
</section>

<section>
  <h2 class="abs welcome-title" style="font-weight:400">WELCOME TO CORVIN SOFTWARE</h2>
  <p class="abs welcome-copy">Corvin Software have developed and continue to support software in over 30 countries, providing real results to hundreds of drilling operations. With decades of hands-on software and well engineering experience, we are uniquely positioned to provide the right solution to our customers.</p>
</section>

<section>
  <div class="abs clients-rule"></div>
  <div class="abs clients-label">Our Clients</div>
  <div class="abs client-row">
    <span class="client">Koruna</span>
    <span class="client"><i></i>GN</span>
    <span class="client">Harlow</span>
    <span class="client">VELO</span>
    <span class="client">Dunt</span>
    <span class="client">Marovel</span>
    <span class="client">FALUMI</span>
    <span class="client">Tarnwick</span>
    <span class="client">Lomond</span>
  </div>
</section>

<footer>
  <div class="abs footer"></div>
  <div class="abs footer-col" style="left:123px">
    <h4>EUROPE</h4>
    18 Fenwick Row<br>Dunmore, DM4 2QP<br>Phone:+44(0)1632 960417<br>Email:eu@corvinsoft.example
  </div>
  <div class="abs footer-col" style="left:308px">
    <h4>NORTH AMERICA</h4>
    18 Fenwick Row<br>Dunmore, DM4 2QP<br>Phone:+44(0)1632 960417<br>Email:eu@corvinsoft.example
  </div>
  <div class="abs footer-col" style="left:496px">
    <h4>WEB SITES</h4>
    Web builder<br>Custom web sites<br>SSL certificates<br>Logo design
  </div>
  <div class="abs partner-badge" aria-label="Partner badge"></div>
  <div class="abs footer-bar"></div>
  <div class="abs copyright">Copyright 2012 Corvin Software | All Rights Reserved | Terms &amp; Conditions | Site map</div>
</footer>

</body>
</html>
```